Business Card Design

We need a business card designed for our new company. Prefer a black card with white logo & writing.

Contact Information for Business Card

Ted Galloway, address: 7-4812 Fernhollow Road, Abbotsford, BC, V3K 8R2, Office Phone: 604-712-3390, Cell: 604-947-2164, Email: ted@resinworkshub.ca

Colors

Designer to choose only greyscale colors for use in the design.

```html
<!DOCTYPE html>
<html lang="en">
<head>
<meta charset="utf-8">
<title>Resinworks Hub – Business Card</title>
<link href="https://fonts.googleapis.com/css2?family=Poppins:wght@300;400;700&display=swap" rel="stylesheet">
<style>
  :root {
    --backdrop: #232325;
    --card: #1c1c1e;
    --card-edge: #2c2c2f;
    --ink: #ffffff;
    --ink-soft: #e4e4e4;
    --rule: #8a8a8a;
  }
  * { box-sizing: border-box; margin: 0; padding: 0; }
  html, body {
    width: 1200px; height: 711px; overflow: hidden;
    background: var(--backdrop);
    font-family: "Poppins", sans-serif;
    color: var(--ink);
  }
  .stage {
    width: 1200px; height: 711px;
    display: flex; align-items: center; justify-content: center; gap: 40px;
  }
  .card {
    position: relative;
    width: 520px; height: 297px;
    background: var(--card);
    border: 1px solid var(--card-edge);
    border-radius: 22px;
    box-shadow: 0 14px 30px rgba(0,0,0,.45);
  }
  .brand {
    display: flex; align-items: center; gap: 10px;
    font-weight: 700; letter-spacing: .5px; color: var(--ink);
  }
  .brand-dot {
    width: 18px; height: 18px; border-radius: 50%;
    border: 3px solid var(--ink);
  }
  .card-front { display: flex; align-items: center; justify-content: center; }
  .card-front .brand { font-size: 30px; }

  .card-back .brand {
    position: absolute; left: 0; width: 255px; top: 0; height: 100%;
    justify-content: center; font-size: 19px;
  }
  .divider {
    position: absolute; left: 258px; top: 58px; width: 1px; height: 180px;
    background: var(--rule);
  }
  .details { position: absolute; left: 285px; top: 56px; width: 220px; }
  .name { font-size: 25px; line-height: 1.1; font-weight: 300; }
  .name b { font-weight: 700; }
  .role { font-size: 12px; font-weight: 300; color: var(--ink-soft); margin-top: 2px; }
  .address { font-size: 12px; font-weight: 300; line-height: 1.45; color: var(--ink-soft); margin-top: 16px; }
  .contacts { list-style: none; margin-top: 14px; }
  .contacts li {
    display: flex; align-items: center; gap: 9px;
    font-size: 12px; font-weight: 300; line-height: 1.8; color: var(--ink-soft);
  }
  .contacts svg { width: 12px; height: 12px; flex: none; }
</style>
</head>
<body>
  <main class="stage">
    <section class="card card-front">
      <div class="brand"><span class="brand-dot"></span>RESINWORKS HUB</div>
    </section>

    <section class="card card-back">
      <div class="brand"><span class="brand-dot"></span>RESINWORKS HUB</div>
      <div class="divider"></div>
      <div class="details">
        <h1 class="name"><b>Ted</b> Galloway</h1>
        <p class="role">Founder &amp; CEO</p>
        <p class="address">7-4812 Fernhollow Road,<br>Abbotsford, BC, V3K 8R2.</p>
        <ul class="contacts">
          <li>
            <svg viewBox="0 0 12 12" fill="none" stroke="#fff" stroke-width="1.2"><path d="M2 1.5h2.2l1 2.5-1.3 1a6 6 0 0 0 3.1 3.1l1-1.3 2.5 1V10a1 1 0 0 1-1 1A9 9 0 0 1 1 2.5a1 1 0 0 1 1-1z"/></svg>
            604-712-3390
          </li>
          <li>
            <svg viewBox="0 0 12 12" fill="none" stroke="#fff" stroke-width="1.2"><rect x="3" y="0.8" width="6" height="10.4" rx="1"/><circle cx="6" cy="9.2" r=".6" fill="#fff"/></svg>
            604-947-2164
          </li>
          <li>
            <svg viewBox="0 0 12 12" fill="none" stroke="#fff" stroke-width="1.1"><circle cx="6" cy="6" r="5"/><path d="M1 6h10M6 1c-2.4 2.8-2.4 7.2 0 10M6 1c2.4 2.8 2.4 7.2 0 10"/></svg>
            www.resinworkshub.ca
          </li>
          <li>
            <svg viewBox="0 0 12 12" fill="none" stroke="#fff" stroke-width="1.2"><rect x="1" y="2.5" width="10" height="7" rx=".8"/><path d="M1.3 3l4.7 3.6L10.7 3"/></svg>
            ted@resinworkshub.ca
          </li>
        </ul>
      </div>
    </section>
  </main>
</body>
</html>
```